BrindleStaffing Business Card Design

We are a staffing company finding positions for dedicated nurses and physicians.

Target Market(s)

Business Professionals

Industry/Entity Type

Staffing

Contact Information for Business Card

Gordon Pratley
Chairman
417 39th Avenue South
SAINT PETERSBURG FL 33712
813-555-4172 Mobile
813-555-8036 Fax
gpratley@brindlestaffing.com
www.brindlestaffing.com

Font styles to use
Sans Serif

Colors
fbee3e
f04a50
f37122

Requirements
Must have
• Logo Attached, see colors below. We'd like to see Yellow, Orange and Red.

```html
<!DOCTYPE html>
<html lang="en">
<head>
<meta charset="utf-8">
<title>BrindleStaffing Business Card</title>
<link rel="stylesheet" href="https://fonts.googleapis.com/css2?family=Lato:wght@400&family=Outfit:wght@500;600;700&display=swap">
<style>
  :root {
    --backdrop: #8b5226;
    --kraft-light: #d2ab78;
    --kraft-mid: #c29563;
    --kraft-dark: #b07f4c;
    --ink: #111111;
    --brand-yellow: #fbee3e;
    --brand-orange: #f37122;
    --brand-red: #f04a50;
  }
  * { margin: 0; padding: 0; box-sizing: border-box; }
  html, body {
    width: 1200px;
    height: 900px;
    overflow: hidden;
  }
  body {
    position: relative;
    background: var(--backdrop);
    font-family: "Lato", sans-serif;
    color: var(--ink);
  }
  .card {
    position: absolute;
    left: 330px;
    width: 557px;
    height: 343px;
    background: radial-gradient(ellipse at 35% 0%, var(--kraft-light) 0%, var(--kraft-mid) 55%, var(--kraft-dark) 100%);
    box-shadow: 3px 4px 6px rgba(0, 0, 0, 0.45);
  }
  .card-front { top: 90px; }
  .card-back { top: 469px; }

  .contact-name {
    position: absolute;
    top: 72px;
    width: 100%;
    text-align: center;
    font-family: "Outfit", sans-serif;
    font-weight: 600;
    font-size: 25px;
    line-height: 30px;
    letter-spacing: 0.2px;
  }
  .contact-title {
    position: absolute;
    top: 104px;
    width: 100%;
    text-align: center;
    font-family: "Outfit", sans-serif;
    font-weight: 500;
    font-size: 12px;
    line-height: 14px;
    letter-spacing: 2px;
    text-transform: uppercase;
  }
  .icon-row {
    position: absolute;
    top: 126px;
    left: 188px;
    width: 180px;
    height: 20px;
  }
  .contact-lines {
    position: absolute;
    top: 152px;
    width: 100%;
    text-align: center;
    font-size: 15px;
    line-height: 20px;
  }
  .divider {
    position: absolute;
    top: 239px;
    left: 187px;
    width: 181px;
    height: 1px;
    background: var(--brand-orange);
  }
  .address-lines {
    position: absolute;
    top: 247px;
    width: 100%;
    text-align: center;
    font-size: 15px;
    line-height: 20px;
  }
  .brand-name {
    position: absolute;
    top: 140px;
    width: 100%;
    text-align: center;
    font-family: "Outfit", sans-serif;
    font-weight: 700;
    font-size: 50px;
    line-height: 60px;
    letter-spacing: -1px;
    white-space: nowrap;
  }
  .brand-dot {
    display: inline-block;
    width: 18px;
    height: 18px;
    margin-right: 12px;
    border-radius: 50%;
    background: var(--brand-orange);
    vertical-align: 6px;
  }
</style>
</head>
<body>
  <section class="card card-front" aria-label="Card front with contact details">
    <h1 class="contact-name">Gordon Pratley</h1>
    <p class="contact-title">Chairman</p>
    <svg class="icon-row" viewBox="0 0 180 20" aria-hidden="true">
      <line x1="0" y1="10" x2="52" y2="10" stroke="#f37122" stroke-width="1"/>
      <line x1="128" y1="10" x2="180" y2="10" stroke="#f37122" stroke-width="1"/>
      <rect x="56" y="1" width="18" height="18" fill="#fbee3e"/>
      <path d="M60 13 q5 -6 10 0 v2 h-3 v-2 h-4 v2 h-3 z M61 8 h8 v2 h-8 z" fill="#111111"/>
      <rect x="81" y="1" width="18" height="18" fill="#f37122"/>
      <rect x="84" y="5" width="12" height="9" fill="none" stroke="#111111" stroke-width="1.4"/>
      <path d="M84 5 l6 5 l6 -5" fill="none" stroke="#111111" stroke-width="1.4"/>
      <rect x="106" y="1" width="18" height="18" fill="#f04a50"/>
      <circle cx="115" cy="10" r="5.5" fill="none" stroke="#111111" stroke-width="1.4"/>
      <path d="M109.5 10 h11 M115 4.5 q-3 5.5 0 11 q3 -5.5 0 -11" fill="none" stroke="#111111" stroke-width="1.1"/>
    </svg>
    <p class="contact-lines">
      813-555-4172 Mobile<br>
      813-555-8036 Fax<br>
      gpratley@brindlestaffing.com<br>
      www.brindlestaffing.com
    </p>
    <div class="divider"></div>
    <p class="address-lines">
      417 39th Avenue South<br>
      SAINT PETERSBURG FL 33712
    </p>
  </section>

  <section class="card card-back" aria-label="Card back with company name">
    <p class="brand-name"><span class="brand-dot" aria-hidden="true"></span>BrindleStaffing</p>
  </section>
</body>
</html>
```